Lo Mara Menu Design Project

This project is pretty straight forward. You will be given 3 files which include the following:
1. Our proposed menu
2. Our Company logo
3. A sample menu on what we are looking for design wise

Your job is to create a visually pleasing menu that is simple, clean and fresh. Please refer to our home website for additional information. (www.lomara-eats.com) Must be in eps or equivalent format.

Target Market(s)

20s to 40s

Industry/Entity Type

It Company

Requirements
Must have
• Company log
Must be in EPS format

```html
<!DOCTYPE html>
<html lang="en">
<head>
<meta charset="utf-8">
<title>Lo Mara Menu – Vegetables, Gluten Free, Mushu &amp; Rice</title>
<link href="https://fonts.googleapis.com/css2?family=Josefin+Sans:ital,wght@0,400;0,600;0,700;1,300;1,400&display=swap" rel="stylesheet">
<style>
  :root {
    --ink: #ffffff;
    --accent: #c1272d;
    --shade-deep: #0d0b0b;
    --shade-mid: #2a2220;
    --shade-warm: #4a3128;
  }
  html, body {
    margin: 0;
    padding: 0;
    width: 1200px;
    height: 1000px;
    overflow: hidden;
    background: var(--shade-deep);
  }
  .menu-spread {
    position: relative;
    width: 1200px;
    height: 1000px;
    overflow: hidden;
    font-family: "Josefin Sans", sans-serif;
    color: var(--ink);
  }
  .food-backdrop {
    position: absolute;
    inset: 0;
    background:
      radial-gradient(ellipse at 30% 75%, rgba(90,55,40,0.75), transparent 55%),
      radial-gradient(ellipse at 75% 35%, rgba(70,45,35,0.7), transparent 50%),
      linear-gradient(160deg, var(--shade-mid) 0%, var(--shade-warm) 45%, var(--shade-deep) 100%);
  }
  .page-divider {
    position: absolute;
    left: 600px;
    top: 0;
    width: 2px;
    height: 1000px;
    background: var(--accent);
  }
  .column {
    position: absolute;
    top: 0;
  }
  .column--left { left: 58px; width: 481px; }
  .column--right { left: 655px; width: 482px; }
  .section-title {
    margin: 0;
    color: var(--accent);
    font-weight: 400;
    font-size: 25px;
    letter-spacing: 0.5px;
    text-align: center;
    text-transform: uppercase;
  }
  .offer-note {
    margin: 26px 0 0;
    text-align: center;
    font-weight: 700;
    font-size: 17.5px;
    line-height: 22.5px;
  }
  .dish-list { margin: 0; padding: 0; list-style: none; }
  .dish { font-size: 17.5px; line-height: 22.6px; }
  .dish-head {
    display: flex;
    justify-content: space-between;
    font-weight: 700;
  }
  .dish-desc {
    font-style: italic;
    font-weight: 300;
    text-align: right;
  }
  .dish-desc--left { text-align: left; }
  .veg-list { margin-top: 44px; }
  .gf-list { margin-top: 11px; }
  .gf-list .dish { margin-bottom: 0; }
  .gf-list .dish-head--plain { font-weight: 400; font-style: italic; }
  .mushu-title { margin-top: 30px; }
  .rice-list { margin-top: 15px; padding-left: 10px; }
  .size-prices { display: flex; gap: 20px; }
  .brand-mark {
    position: absolute;
    bottom: 28px;
    color: var(--accent);
    font-weight: 700;
    font-size: 15px;
    letter-spacing: 0.5px;
  }
  .brand-mark--left { left: 20px; }
  .brand-mark--right { right: 12px; }
</style>
</head>
<body>
<div class="menu-spread">
  <div class="food-backdrop" role="img" aria-label="Darkened close-up photograph of sesame-topped glazed dishes on a patterned plate with chopsticks"></div>
  <div class="page-divider"></div>

  <section class="column column--left">
    <h2 class="section-title" style="margin-top:24px">Vegetables</h2>
    <p class="offer-note">Enjoy a Half Chinese Chicken Salad or Plain Fried<br>Rice with any entrée for $5.50<br>Can add Tofu for $1.50</p>
    <ul class="dish-list veg-list">
      <li class="dish"><div class="dish-head"><span>Fragrant Vegetables</span><span>8.95</span></div>
        <div class="dish-desc">Mixed vegetables with white wine, curry, garlic, black<br>bean, kungpao, or vegetarian sauce.</div></li>
      <li class="dish"><div class="dish-head"><span>Vegetable Lettuce Wraps</span><span>9.95</span></div>
        <div class="dish-desc">Black mushrooms, bell peppers, water chestnuts, smoked<br>tofu, pine nuts, and white crunchies. Served with four let-<br>tuce cups.</div></li>
      <li class="dish"><div class="dish-head"><span>Szechuan String Beans</span><span>8.95</span></div>
        <div class="dish-desc">Blue lake green beans and garlic sautéed with pickled<br>szechwan vegetables.</div></li>
      <li class="dish"><div class="dish-head"><span>Tofu With Black Mushrooms</span><span>7.95</span></div>
        <div class="dish-desc">Fried tofu triangles sautéed with scallions, black mush-<br>rooms, water chestnuts, and cabbage.</div></li>
      <li class="dish"><div class="dish-head"><span>Bok Choy With Black Mushrooms</span><span>6.95</span></div>
        <div class="dish-desc">Baby bokchoy and black mushrooms sautéed in a<br>brown sauce.</div></li>
      <li class="dish"><div class="dish-head"><span>Spicy Garlic Eggplant</span><span>8.95</span></div>
        <div class="dish-desc">Sautéed chinese eggplant, red onions, and scallions in<br>a spicy garlic sauce.</div></li>
      <li class="dish"><div class="dish-head"><span>Salt And Pepper Tofu</span><span>7.95</span></div>
        <div class="dish-desc">Lightly battered soft tofu cubes with a pepper spice<br>with bell peppers and white crunchies.</div></li>
      <li class="dish"><div class="dish-head"><span>Spinach With Garlic</span><span>6.95</span></div>
        <div class="dish-desc">Sautéed spinach with garlic.</div></li>
    </ul>
  </section>

  <section class="column column--right">
    <h2 class="section-title" style="margin-top:24px">Gluten Free</h2>
    <ul class="dish-list gf-list">
      <li class="dish"><div class="dish-head dish-head--plain"><span>XXXXXXXX</span><span>zzzz</span></div>
        <div class="dish-desc">yyyyyyyyyyyyyyyyyyyyyyyyyyyyyyyyyyyyyyyyyyyyyyyyyyyy<br>yyyyyyyyyyyyyyy</div></li>
      <li class="dish"><div class="dish-head"><span>XXXXXXXX</span><span>zzzz</span></div>
        <div class="dish-desc">yyyyyyyyyyyyyyyyyyyyyyyyyyyyyyyyyyyyyyyyyyyyyyyyyyyy<br>yyyyyyyyyyyyyyy</div></li>
      <li class="dish"><div class="dish-head"><span>XXXXXXXX</span><span>zzzz</span></div>
        <div class="dish-desc">yyyyyyyyyyyyyyyyyyyyyyyyyyyyyyyyyyyyyyyyyyyyyyyyyyyy<br>yyyyyyyyyyyyyyy</div></li>
      <li class="dish"><div class="dish-head"><span>XXXXXXXX</span><span>zzzz</span></div>
        <div class="dish-desc">yyyyyyyyyyyyyyyyyyyyyyyyyyyyyyyyyyyyyyyyyyyyyyyyyyyy<br>yyyyyyyyyyyyyyy</div></li>
      <li class="dish"><div class="dish-head"><span>XXXXXXXX</span><span>zzzz</span></div>
        <div class="dish-desc">yyyyyyyyyyyyyyyyyyyyyyyyyyyyyyyyyyyyyyyyyyyyyyyyyyyy<br>yyyyyyyyyyyyyyy</div></li>
      <li class="dish"><div class="dish-head"><span>XXXXXXXX</span><span>zzzz</span></div>
        <div class="dish-desc">Yyyyyyyyyyyyyyyyyyyyyyyyyyyyyyyyyyyyyyyyyyyyyyyyyyyy<br>yyyyyyyyyyyyyyy</div></li>
    </ul>

    <h2 class="section-title mushu-title">Mushu &amp; Rice</h2>
    <ul class="dish-list rice-list">
      <li class="dish"><div class="dish-head"><span>Crab And Asparagus Fried Rice</span><span>13.95</span></div>
        <div class="dish-desc">White fried rice with dungeness crab, asparagus, and<br>egg white topped with fried onions. No soy sauce.</div></li>
      <li class="dish"><div class="dish-head"><span>Yang Chow Rice</span><span>9.25</span></div>
        <div class="dish-desc">White fried rice with shrimp, barbeque pork, peas, car-<br>rots, and eggs. No soy sauce.</div></li>
      <li class="dish"><div class="dish-head"><span>Mushu</span><span>7.95</span></div>
        <div class="dish-desc">Chicken, pork, or vegetable mushu with sautéed veg-<br>etables, mushrooms, and eggs. Wrapped in two thin<br>pancakes. For shrimp, add $1.00.</div></li>
      <li class="dish"><div class="dish-head"><span>Fried Rice</span><span>7.95</span></div>
        <div class="dish-desc">Chicken, pork, or vegetable with eggs, scallions, and<br>fried rice sauce. For beef or shrimp, add $1.00. For soft<br>tofu, add $1.00. For deep-Fried tofu, add $1.50.</div></li>
      <li class="dish"><div class="dish-head"><span>Steamed Rice</span><span class="size-prices" style="margin-right:52px"><span>SM.</span><span>LG.</span></span></div>
        <div class="dish-head" style="font-weight:700"><span class="dish-desc dish-desc--left">Choice of White or Brown.</span><span class="size-prices"><span>1.25</span><span>1.75</span></span></div></li>
    </ul>
  </section>

  <div class="brand-mark brand-mark--left">LO MARA</div>
  <div class="brand-mark brand-mark--right">LO MARA</div>
</div>
</body>
</html>
```